House-share and Room Rental Website (With Focus on the Bedroom Landing Page)

Looking for website design for our House-share (executive accommodation) and room rental business.

Our company name is: Lodgivo could also be written as LodGivo or lodgivo. Either is fine .. just looking for a nice clean catchy logo to go with the design.

EXAMPLES
These are examples of other websites in this field that are doing well. this is a kind of baseline.
https://nestpartners-example.com.au/
https://www.bunkora-example.com/
https://www.dwelzy-example.com/
https://www.habiquo-example.net/
https://www.cohabiscout-example.com.au/

Our business model is to rent rooms to people looking for high-quality accommodation. We fill the gap between those looking to rent rooms and those with rooms to rent. However, our model is slightly different from those already on the market as we looking to fill a massive gap in the market delivering upmarket rooms for rent.(Executive Accommodation) also in the back end will be coupled with a self management process in the back end.

We offer executive style accommodation that stands out above the rest. With special extras like fire safety.. and management processes that create happier homes. We are looking for a web design package that can help us grow and scale our business. We need a design that is captivating

Our MAIN focus is having a room landing page that stands out from the rest... The core of our business will rely on the promotion of the rooms in a share house... so the whole design relies on the BEDROOM landing page to drive results.

Target Market(s)

We have 2 markets we are aiming at ... the first market is people offering rooms to rent who want the highest rental return. The second market is people looking to rent safe, high-quality rooms, in houses that are well managed and looked after.

Industry/Entity Type

Share Economy

Logo Text

LodGivo

Number of Pages Required

5+ page

Font styles to use
Sans Serif

Colors
3276b5

Requirements
Must have
• A messaging system whereby we can create direct communication between those offering rooms and those looking for rooms.
• A call to action that says " Schedule an Inspection"
• Landing page for promoting rooms
• A home page for showing stock.
• Profile page for those selling rooms
• Profile page for those looking for rooms.
• A scheduling calendar for booking inspections
Nice to have
• Pages where new residents can lock in a room.. pay bond and rents.. and sign contracts
• Notifications
• SMS capabilities in the backend.
Should not have
• No script or handwriting fonts.

```html
<!DOCTYPE html>
<html lang="en">
<head>
<meta charset="utf-8">
<title>LodGivo – Classic bed room</title>
<link href="https://fonts.googleapis.com/css2?family=Dosis:wght@300;400;500;600;700&display=swap" rel="stylesheet">
<style>
  :root {
    --brand: #3276b5;
    --header-bg: #333333;
    --ink: #2b2b2b;
    --muted: #8a8a8a;
    --rule: #d6d6d6;
    --card-bg: #f2f2f2;
    --field-bg: #f9f9f9;
    --online: #3a9a3a;
    --white: #ffffff;
  }
  * { box-sizing: border-box; margin: 0; padding: 0; }
  html, body { width: 1200px; height: 1000px; overflow: hidden; background: var(--white); }
  body { position: relative; font-family: "Dosis", sans-serif; color: var(--ink); }

  .site-header { position: absolute; left: 0; top: 0; width: 1200px; height: 90px; background: var(--header-bg); }
  .back-link { position: absolute; left: 48px; top: 36px; }
  .brand-name { position: absolute; left: 0; width: 100%; top: 28px; text-align: center; font-size: 27px; font-weight: 600; color: var(--brand); letter-spacing: 1px; }

  .gallery { position: absolute; left: 0; top: 90px; width: 1200px; height: 390px; overflow: hidden; }
  .gallery-side { position: absolute; top: 0; height: 390px; opacity: .45; }
  .gallery-side.prev { left: 0; width: 266px; background: linear-gradient(180deg, #e8e8e6 0%, #cfccc8 55%, #ebe9e6 100%); }
  .gallery-side.next { left: 938px; width: 262px; background: linear-gradient(180deg, #f4f4f4 0%, #e4e4e4 60%, #f0f0f0 100%); }
  .gallery-main { position: absolute; left: 266px; top: 0; width: 672px; height: 390px;
    background: linear-gradient(180deg, #f3f3f3 0%, #e9ebee 30%, #dcdedf 60%, #9a958f 85%, #8d8782 100%); }
  .gallery-arrow { position: absolute; top: 171px; width: 48px; height: 48px; border: 1px solid #333; border-radius: 50%; display: flex; align-items: center; justify-content: center; }
  .gallery-arrow.prev { left: 241px; }
  .gallery-arrow.next { left: 913px; }
  .gallery-count { position: absolute; left: 771px; top: 346px; width: 167px; height: 44px; background: var(--header-bg); color: #ddd; font-size: 15px; display: flex; align-items: center; justify-content: center; gap: 6px; }
  .gallery-count b { color: var(--white); font-weight: 600; }

  .listing-title { position: absolute; left: 109px; top: 536px; font-size: 41px; font-weight: 300; color: var(--ink); }
  .listing-address { position: absolute; left: 110px; top: 592px; font-size: 14px; color: #444; }
  .listing-address b { font-weight: 500; color: var(--ink); }
  .map-link { position: absolute; left: 110px; top: 618px; font-size: 13px; color: var(--brand); display: flex; align-items: center; gap: 5px; }

  .price { position: absolute; right: 467px; top: 557px; font-size: 22px; font-weight: 700; color: var(--brand); }
  .contract-note { position: absolute; right: 467px; top: 594px; font-size: 12px; color: var(--muted); }
  .utilities-note { position: absolute; right: 467px; top: 618px; font-size: 13px; color: #555; }

  .rule { position: absolute; left: 110px; width: 623px; height: 1px; background: var(--rule); }

  .feature { position: absolute; width: 156px; text-align: center; font-size: 14px; color: var(--muted); }
  .feature b { color: #444; font-weight: 600; }
  .feature svg { display: block; margin: 0 auto; }

  .host-card { position: absolute; left: 778px; top: 548px; width: 311px; height: 421px; background: var(--card-bg); }
  .host-name { position: absolute; right: 164px; top: 52px; font-size: 19px; font-weight: 700; color: var(--ink); }
  .host-status { position: absolute; right: 164px; top: 79px; font-size: 13px; color: var(--online); }
  .host-phone { position: absolute; right: 164px; top: 111px; font-size: 13px; color: #444; }
  .host-phone span { color: var(--muted); }
  .host-avatar { position: absolute; left: 165px; top: 38px; width: 98px; height: 98px; border: 2px solid var(--white);
    background: linear-gradient(180deg, #7cc3d8 0%, #9fd0dc 50%, #d9b3a0 100%); box-shadow: 0 4px 10px rgba(0,0,0,.25); }
  .message-field { position: absolute; left: 48px; top: 185px; width: 215px; height: 118px; background: var(--field-bg); padding: 12px 22px; font-size: 12px; color: var(--muted); }
  .send-button { position: absolute; left: 48px; top: 325px; width: 215px; height: 46px; background: var(--brand); color: var(--white); font-size: 15px; font-weight: 500; display: flex; align-items: center; justify-content: center; box-shadow: 0 6px 12px rgba(50,118,181,.25); }
</style>
</head>
<body>
  <header class="site-header">
    <svg class="back-link" width="32" height="20" viewBox="0 0 32 20" fill="none" stroke="#9a9a9a" stroke-width="1.5"><path d="M31 10H2M10 2L2 10l8 8"/></svg>
    <div class="brand-name">LodGivo</div>
  </header>

  <section class="gallery">
    <div class="gallery-side prev" role="img" aria-label="Previous photo: bright white kitchen"></div>
    <div class="gallery-main" role="img" aria-label="Photo of a bright bedroom with a double bed, large window and pendant light"></div>
    <div class="gallery-side next" role="img" aria-label="Next photo: white bathroom vanity"></div>
    <div class="gallery-arrow prev"><svg width="12" height="16" viewBox="0 0 12 16" fill="none" stroke="#333" stroke-width="1.5"><path d="M8 2L2 8l6 6"/></svg></div>
    <div class="gallery-arrow next"><svg width="12" height="16" viewBox="0 0 12 16" fill="none" stroke="#333" stroke-width="1.5"><path d="M4 2l6 6-6 6"/></svg></div>
    <div class="gallery-count"><span><b>3</b>/12</span><span>View Gallery</span></div>
  </section>

  <h1 class="listing-title">Classic bed room</h1>
  <p class="listing-address">48 Wattle Ln, <b>Sydney</b></p>
  <p class="map-link"><svg width="12" height="16" viewBox="0 0 12 16" fill="none" stroke="#3276b5" stroke-width="1.2"><path d="M6 15S1 9 1 6a5 5 0 0110 0c0 3-5 9-5 9z"/><circle cx="6" cy="6" r="1.8"/></svg>Location map</p>

  <p class="price">350 AUD</p>
  <p class="contract-note">( Minimum 3 months contract )</p>
  <p class="utilities-note">Utilities excluded</p>

  <div class="rule" style="top:671px"></div>

  <div class="feature" style="left:109px;top:730px">
    <svg width="40" height="40" viewBox="0 0 40 40" fill="none" stroke="#3276b5" stroke-width="1.3"><circle cx="11" cy="5" r="3"/><path d="M6 12h10v12h-2v14h-6V24H6z"/><circle cx="29" cy="5" r="3"/><path d="M26 11h6l4 15h-4v12h-6V26h-4z"/></svg>
    <div style="margin-top:14px">Gender - <b>Male</b></div>
  </div>
  <div class="feature" style="left:265px;top:730px">
    <svg width="40" height="40" viewBox="0 0 40 40" fill="none" stroke="#3276b5" stroke-width="1.3"><path d="M2 14L20 2l18 12v24H2z"/><circle cx="20" cy="19" r="4"/><path d="M12 32c1-5 4-7 8-7s7 2 8 7z"/></svg>
    <div style="margin-top:14px">Room type - <b>Private</b></div>
  </div>
  <div class="feature" style="left:421px;top:730px">
    <svg width="40" height="40" viewBox="0 0 40 40" fill="none" stroke="#3276b5" stroke-width="1.3"><rect x="1" y="1" width="38" height="38"/><path d="M8 8l8 8M8 8h5M8 8v5M32 8l-8 8M32 8h-5M32 8v5M8 32l8-8M8 32h5M8 32v-5M32 32l-8-8M32 32h-5M32 32v-5"/></svg>
    <div style="margin-top:14px">Size of room - <b>30</b> sqm</div>
  </div>
  <div class="feature" style="left:577px;top:730px">
    <svg width="40" height="40" viewBox="0 0 40 40" fill="none" stroke="#3276b5" stroke-width="1.3"><rect x="1" y="1" width="38" height="38"/><path d="M14 31V9h8a6 6 0 010 12h-8" stroke-width="2"/></svg>
    <div style="margin-top:14px">Parking - <b>Private</b></div>
  </div>

  <div class="feature" style="left:109px;top:850px">
    <svg width="40" height="32" viewBox="0 0 40 32" fill="none" stroke="#3276b5" stroke-width="1.3"><rect x="4" y="4" width="32" height="12"/><rect x="8" y="8" width="10" height="7"/><rect x="22" y="8" width="10" height="7"/><rect x="2" y="16" width="36" height="9"/><path d="M4 25v5M36 25v5"/></svg>
    <div style="margin-top:10px;font-size:13px;color:#444">Bed size - <b>Double</b></div>
  </div>
  <div class="feature" style="left:265px;top:845px">
    <svg width="40" height="38" viewBox="0 0 40 38" fill="none" stroke="#3276b5" stroke-width="1.3"><rect x="1" y="1" width="38" height="36"/><path d="M1 7h38M4 4h1M7 4h1M10 4h1"/><path d="M10 20a14 14 0 0120 0M13 24a9 9 0 0114 0M16 28a5 5 0 018 0"/><circle cx="20" cy="31" r="1"/></svg>
    <div style="margin-top:12px;font-size:13px;color:#444">internet speed - <b>High</b></div>
  </div>
  <div class="feature" style="left:421px;top:850px">
    <svg width="40" height="32" viewBox="0 0 40 32" fill="none" stroke="#3276b5" stroke-width="1.3"><path d="M6 16V5a3 3 0 016 0v1"/><path d="M10 8h5"/><path d="M2 16h36v4a8 8 0 01-8 8H10a8 8 0 01-8-8z"/><path d="M9 28l-2 3M31 28l2 3"/></svg>
    <div style="margin-top:10px">Bathroom - <b>Private</b></div>
  </div>
  <div class="feature" style="left:577px;top:850px">
    <svg width="44" height="32" viewBox="0 0 44 32" fill="none" stroke="#3276b5" stroke-width="1.3"><rect x="4" y="17" width="36" height="6"/><path d="M32 17v6"/><path d="M6 30L38 8"/><path d="M6 2c2 2-2 4 0 6M10 2c2 2-2 4 0 6"/></svg>
    <div style="margin-top:10px;font-size:13px;color:#444">Smoking - <b>Non</b></div>
  </div>

  <div class="rule" style="top:969px"></div>

  <aside class="host-card">
    <p class="host-name">Tom Ferris</p>
    <p class="host-status">Online</p>
    <p class="host-phone">0412 883 207 <span>: Mobile</span></p>
    <div class="host-avatar" role="img" aria-label="Host profile photo"></div>
    <div class="message-field">Write message</div>
    <div class="send-button">SEND</div>
  </aside>
</body>
</html>
```